Business Cards Design for the electrical wholesaler: clean bold dynamic :)

We need a business card design that would follow our latest brand guidelines. As an electrical wholesaler we want to bring a fresh look and feel into the industry. The design should be clean bold and dynamic. It should come alive with the renewed energy of our green colour. Our grey colour should keep things balanced and complement the notion of maturity and responsibility. We employ Lato as a corporate font however are not bound by this font and we’re open to interpretation here.

Target Market(s)

Electrical contractors

Industry/Entity Type

Business

Contact Information for Business Card

Logo
Name & Surname: Halyna Dorosh
Job Title: Director of Marketing
Email: halya.dorosh@quillmail.example
Cell phone: XXX.XXX.XXXX
Address: 20517 - 87 Ave. Edmonton, AB, Canada. T6K 4N8
Business Phone: 780.555.0184
Website: www.brovix.example

Font styles to use
Other font styles liked:
• Lato

Requirements
Must have
• Logo & website
Nice to have
• Brand elements - some of them you may find in the attached Brand Guidelines (e.g. three lines on the background signifying "W")

```html
<!DOCTYPE html>
<html lang="en">
<head>
<meta charset="utf-8">
<title>Brovix Business Cards</title>
<link rel="stylesheet" href="https://fonts.googleapis.com/css2?family=Work+Sans:wght@400;500;600&display=swap">
<style>
  :root {
    --page-bg: #141414;
    --card-top: #2c2c2c;
    --card-bottom: #1e1e1e;
    --brand-green: #7dc242;
    --brand-grey: #c9c9c9;
    --text-light: #f2f2f2;
  }
  * { box-sizing: border-box; margin: 0; padding: 0; }
  html, body {
    width: 1200px; height: 900px; overflow: hidden;
    background: var(--page-bg);
    font-family: "Work Sans", "Lato", sans-serif;
  }
  .sheet {
    position: relative; width: 1200px; height: 900px;
    display: flex; flex-direction: column; align-items: center;
    justify-content: center; gap: 40px;
  }
  .card {
    position: relative; width: 680px; height: 390px;
    background: linear-gradient(150deg, var(--card-top), var(--card-bottom));
    border-bottom: 8px solid var(--brand-green);
    box-shadow: 0 14px 30px rgba(0,0,0,.55);
  }
  .brand-name {
    font-weight: 500; color: var(--brand-grey);
    letter-spacing: -1px; line-height: 1;
  }
  .card--front { display: flex; align-items: center; justify-content: center; }
  .card--front .brand-name { font-size: 88px; }
  .card--back { display: flex; align-items: center; }
  .back-brand {
    width: 330px; display: flex; justify-content: center;
  }
  .back-brand .brand-name { font-size: 66px; }
  .divider {
    width: 2px; height: 200px; background: var(--brand-green);
  }
  .contact {
    padding-left: 42px; color: var(--text-light);
    font-size: 19px; line-height: 1.35;
  }
  .contact-name {
    color: var(--brand-green); font-weight: 600; font-size: 30px;
    line-height: 1.05;
  }
  .contact-title { font-size: 20px; margin-bottom: 16px; }
  .contact-address { margin-bottom: 14px; }
  .contact-line { display: flex; align-items: center; gap: 12px; }
  .contact-line svg { width: 14px; height: 14px; flex: none; }
</style>
</head>
<body>
<main class="sheet">
  <section class="card card--front">
    <span class="brand-name">brovix</span>
  </section>

  <section class="card card--back">
    <div class="back-brand"><span class="brand-name">brovix</span></div>
    <div class="divider"></div>
    <div class="contact">
      <p class="contact-name">Halyna Dorosh</p>
      <p class="contact-title">Founder</p>
      <p class="contact-address">20517 87ave<br>T6K4N8 Edmonton, Alberta</p>
      <p class="contact-line">
        <svg viewBox="0 0 16 16" aria-hidden="true"><path d="M4 1l3 3-2 2c1 2 3 4 5 5l2-2 3 3-2 2C7 14 2 9 1 3z" fill="#7dc242"/></svg>
        780.555.0184
      </p>
      <p class="contact-line">
        <svg viewBox="0 0 16 16" aria-hidden="true"><rect x="1.5" y="3.5" width="13" height="9" fill="none" stroke="#7dc242" stroke-width="1.5"/><path d="M1.5 3.5L8 9l6.5-5.5" fill="none" stroke="#7dc242" stroke-width="1.5"/></svg>
        hello@brovix.example
      </p>
      <p class="contact-line">
        <svg viewBox="0 0 16 16" aria-hidden="true"><circle cx="8" cy="8" r="6.5" fill="none" stroke="#7dc242" stroke-width="1.5"/><ellipse cx="8" cy="8" rx="3" ry="6.5" fill="none" stroke="#7dc242" stroke-width="1.2"/><path d="M1.5 8h13" stroke="#7dc242" stroke-width="1.2"/></svg>
        www.brovix.example
      </p>
    </div>
  </section>
</main>
</body>
</html>
```